A resume/portfolio website for myself

I'm an independent software contractor, architect, tech trainer. I need a web site to present myself. Many ready to use portfolio designs are too artistic and focused on presenting design skills of the person. I like a nice website but the content should be a little less graphic than if you would present a graphic designer. Content could be presentation of me, core skill qualities and services and resume. Potentially a page with my tech courses in the longer run

```html
<!DOCTYPE html>
<html lang="en">
<head>
<meta charset="utf-8">
<title>Anders Holt — Software Contractor, Architect, Tech Trainer</title>
<link rel="stylesheet" href="https://fonts.googleapis.com/css2?family=Archivo:wght@400;600;700;800;900&family=Raleway:ital,wght@0,300;0,400;0,500;0,600;0,700;1,400&display=swap">
<style>
:root{
  --cyan:#1cc7ea;
  --dark:#484647;
  --ink:#2f2f2f;
  --heading:#454545;
  --muted:#7a7a7a;
  --white:#ffffff;
  --footer:#232323;
  --track:#d9d9d9;
}
*{box-sizing:border-box;margin:0;padding:0}
html,body{width:1200px;height:4695px;overflow:hidden}
body{position:relative;background:var(--white);font-family:"Raleway",Arial,sans-serif;color:var(--ink)}
.abs{position:absolute}
section,header,footer{position:absolute;left:0;width:1200px}

/* hero */
.hero{top:0;height:642px;background:var(--white);overflow:hidden}
.hero-photo{left:0;top:0;width:660px;height:642px;background:radial-gradient(ellipse at 35% 35%,#d9d9d9 0%,#a9a9a9 45%,#ececec 80%,#fafafa 100%)}
.nav{top:46px;left:388px;font-size:14px;color:#555;display:flex}
.nav a{position:absolute;white-space:nowrap;text-decoration:none;color:#555}
.nav-divider{left:1044px;top:40px;width:2px;height:28px;background:var(--cyan)}
.nav-search{left:1066px;top:44px}
.hero-name{left:520px;width:600px;top:218px;text-align:center;font-family:"Archivo",Arial,sans-serif;font-weight:900;font-size:94px;line-height:96px;color:var(--heading);letter-spacing:1px}
.btn{display:flex;align-items:center;justify-content:center;background:var(--cyan);color:#1f2d3a;font-family:"Archivo",Arial,sans-serif;font-weight:600;font-size:13px;border-radius:22px;text-transform:uppercase}
.hero-btn{left:704px;top:454px;width:224px;height:40px}

/* about */
.about{top:642px;height:647px;background:var(--dark);color:var(--white)}
.eyebrow{left:111px;top:108px;color:var(--cyan);font-size:22px;font-weight:500;letter-spacing:1px}
.eyebrow-line{left:246px;top:122px;width:64px;height:1px;background:var(--cyan)}
.about-title{left:100px;width:460px;top:175px;text-align:center;font-size:26px;line-height:40px;font-weight:400;letter-spacing:.5px}
.about-text{left:111px;width:425px;top:305px;font-family:"Archivo",Arial,sans-serif;font-size:13.4px;line-height:22px}
.years-num{left:198px;top:455px;font-size:92px;line-height:92px;font-weight:300;color:var(--cyan);font-family:"Archivo",Arial,sans-serif}
.years-label{left:325px;top:482px;font-family:"Archivo",Arial,sans-serif;font-weight:600;font-size:18px;line-height:26px}
.query{left:627px;top:172px;font-family:"Archivo",Arial,sans-serif;font-weight:800;font-size:44px;line-height:52px}
.contact-label{left:627px;top:314px;font-family:"Archivo",Arial,sans-serif;font-weight:600;font-size:18px}
.contact-link{left:622px;font-family:"Archivo",Arial,sans-serif;font-weight:700;color:var(--cyan)}
.email{top:362px;font-size:19px}
.phone{top:425px;font-size:25px}
.arrow{left:894px}
.social{top:494px;width:38px;height:38px;border-radius:50%;border:1.5px solid #cfcfcf}
.social.active{background:var(--cyan);border-color:var(--cyan)}

/* work */
.work-card{left:111px;top:1402px;width:977px;height:1507px;background:var(--white);box-shadow:0 0 14px rgba(0,0,0,.14)}
.work-title{left:0;width:977px;top:50px;text-align:center;font-size:22px;letter-spacing:1.5px;color:var(--ink)}
.work-rule{left:430px;top:88px;width:116px;height:1px;background:#ccc}
.timeline-line{left:336px;top:166px;width:1px;height:1150px;background:#cfd8dc}
.job{left:0;width:977px;height:230px}
.job-role{left:39px;top:0;color:var(--cyan);font-family:"Archivo",Arial,sans-serif;font-weight:600;font-size:20px;letter-spacing:.6px}
.job-date{left:39px;top:34px;color:#666;font-family:"Archivo",Arial,sans-serif;font-size:15px}
.job-dot{left:325px;top:2px;width:23px;height:23px;border-radius:50%;border:2px solid var(--cyan);background:var(--white)}
.job-dot::after{content:"";position:absolute;left:5px;top:5px;width:9px;height:9px;border-radius:50%;background:var(--cyan)}
.job-company{left:376px;top:2px;font-family:"Archivo",Arial,sans-serif;font-size:17px;color:var(--ink)}
.job-summary{left:376px;top:40px;font-size:15px;color:#333}
.job-detail{left:377px;top:80px;width:440px;font-size:13px;line-height:22px;font-style:italic;color:#666}
.job-pin{left:823px;top:0}
.job-place{left:851px;top:4px;font-family:"Archivo",Arial,sans-serif;font-size:12px;color:#555}

/* skills */
.skills{top:3021px;height:791px;background:var(--dark);color:var(--white)}
.section-head{font-size:22px;letter-spacing:1px;font-weight:500}
.degree{left:111px;color:var(--cyan);font-family:"Archivo",Arial,sans-serif;font-weight:600;font-size:20px;letter-spacing:.5px}
.school{left:111px;font-family:"Archivo",Arial,sans-serif;font-size:16px}
.period{left:111px;font-family:"Archivo",Arial,sans-serif;font-size:13px}
.rule{height:1px;background:#666}
.vrule{left:587px;top:106px;width:1px;height:574px;background:#5e5c5d}
.pill{height:40px;font-size:13px}
.skill-name{left:605px;color:var(--cyan);font-family:"Archivo",Arial,sans-serif;font-weight:600;font-size:20px;letter-spacing:.5px}
.skill-level{left:605px;font-family:"Archivo",Arial,sans-serif;font-size:14px}
.skill-desc{left:605px;width:430px;font-size:13px;line-height:22px;color:#9a9a9a}
.bar{left:605px;width:483px;height:6px;border:1px solid var(--track);background:transparent}
.bar-fill{left:-1px;top:-1px;height:6px;background:var(--cyan)}

/* portfolio */
.portfolio{top:3812px;height:800px;background:var(--white)}
.portfolio-title{left:111px;top:106px;font-size:24px;letter-spacing:1px;color:var(--ink)}
.shot{border-radius:2px}
.view-more{left:487px;top:645px;width:226px;height:44px}

.site-footer{top:4612px;height:83px;background:var(--footer);color:var(--white);font-family:"Archivo",Arial,sans-serif;font-size:13px;display:flex;align-items:center;justify-content:center}
</style>
</head>
<body>

<header class="hero">
  <div class="abs hero-photo" role="img" aria-label="Black and white portrait photograph of Anders Holt"></div>
  <nav class="abs nav" style="left:0;top:0">
    <a style="left:388px;top:46px">Experience</a>
    <a style="left:509px;top:46px">Education</a>
    <a style="left:620px;top:46px">Skills</a>
    <a style="left:698px;top:46px">Accomplishments</a>
    <a style="left:864px;top:46px">Portfolio</a>
    <a style="left:966px;top:46px">Contact</a>
  </nav>
  <div class="abs nav-divider"></div>
  <svg class="abs nav-search" width="20" height="20" viewBox="0 0 20 20" aria-label="Search"><circle cx="8" cy="8" r="5.5" fill="none" stroke="#555" stroke-width="1.6"/><line x1="12" y1="12" x2="17" y2="17" stroke="#555" stroke-width="1.6"/></svg>
  <h1 class="abs hero-name">ANDERS<br>HOLT</h1>
  <a class="abs btn hero-btn">Download my resume</a>
</header>

<section class="about">
  <div class="abs eyebrow">ABOUT ME</div>
  <div class="abs eyebrow-line"></div>
  <h2 class="abs about-title">I'M AN INDEPENDENT SOFTWARE CONTRACTOR, ARCHITECT, TECH TRAINER</h2>
  <p class="abs about-text">Sed ut perspiciatis unde omnis iste natus error sit voluptatem accusantium doloremque laudantium, totam rem aperiam, sdjk eaque ipsa quae ab illo inventore veritatis et quasi architecto beatae vitae dicta sunt explicabo. Nemo enim ipsam volupta tem quia voluptas sit aspernatur aut odit aut fugit, sed quia skliosej consequuntur magni dolores eos qui ratione.</p>
  <div class="abs years-num">20</div>
  <div class="abs years-label">Years Of<br>Experience</div>

  <h2 class="abs query">ANY TYPE OF QUERY<br>&amp; DISCUSSION.</h2>
  <div class="abs contact-label">Let's Contact me</div>
  <a class="abs contact-link email">anders.holt@mail.example</a>
  <svg class="abs arrow" style="top:364px" width="28" height="20" viewBox="0 0 28 20"><path d="M2 10H25M17 3l8 7-8 7" fill="none" stroke="#1cc7ea" stroke-width="2"/></svg>
  <a class="abs contact-link phone">555 010 4821</a>
  <svg class="abs arrow" style="top:432px" width="28" height="20" viewBox="0 0 28 20"><path d="M2 10H25M17 3l8 7-8 7" fill="none" stroke="#1cc7ea" stroke-width="2"/></svg>
  <div class="abs social" style="left:617px" aria-label="Social profile"></div>
  <div class="abs social active" style="left:666px" aria-label="Social profile"></div>
  <div class="abs social" style="left:714px" aria-label="Social profile"></div>
  <div class="abs social" style="left:763px" aria-label="Social profile"></div>
</section>

<main>
  <div class="abs work-card">
    <h2 class="abs work-title">WORK EXPERIENCES</h2>
    <div class="abs work-rule"></div>
    <div class="abs timeline-line"></div>

    <article class="abs job" style="top:152px">
      <div class="abs job-role">SENIOR CONSULTANT</div><div class="abs job-date">Mar 2018 - Present</div>
      <div class="abs job-dot"></div>
      <div class="abs job-company">Nordvik Systems</div>
      <div class="abs job-summary">Daudantium totam rem aperiam sdjk eaque ipsa quae</div>
      <p class="abs job-detail">Sed ut perspiciatis unde omnis iste natus error sit voluptatem accusantium doloremque laudantium, totam rem aperiam, sdjk eaque ipsa quae ab illo inventore</p>
      <svg class="abs job-pin" width="18" height="24" viewBox="0 0 18 24"><path d="M9 1C4.6 1 1.5 4.3 1.5 8.5 1.5 14 9 23 9 23s7.5-9 7.5-14.5C16.5 4.3 13.4 1 9 1z" fill="#555"/><circle cx="9" cy="8.5" r="3" fill="#fff"/></svg>
      <div class="abs job-place">Vestby</div>
    </article>

    <article class="abs job" style="top:382px">
      <div class="abs job-role">SENIOR CONSULTANT</div><div class="abs job-date">Mar 2018 - Present</div>
      <div class="abs job-dot"></div>
      <div class="abs job-company">Nordvik Systems</div>
      <div class="abs job-summary">Daudantium totam rem aperiam sdjk eaque ipsa quae</div>
      <p class="abs job-detail">Sed ut perspiciatis unde omnis iste natus error sit voluptatem accusantium doloremque laudantium, totam rem aperiam, sdjk eaque ipsa quae ab illo inventore</p>
      <svg class="abs job-pin" width="18" height="24" viewBox="0 0 18 24"><path d="M9 1C4.6 1 1.5 4.3 1.5 8.5 1.5 14 9 23 9 23s7.5-9 7.5-14.5C16.5 4.3 13.4 1 9 1z" fill="#555"/><circle cx="9" cy="8.5" r="3" fill="#fff"/></svg>
      <div class="abs job-place">Vestby</div>
    </article>

    <article class="abs job" style="top:612px">
      <div class="abs job-role">SENIOR CONSULTANT</div><div class="abs job-date">Mar 2018 - Present</div>
      <div class="abs job-dot"></div>
      <div class="abs job-company">Nordvik Systems</div>
      <div class="abs job-summary">Daudantium totam rem aperiam sdjk eaque ipsa quae</div>
      <p class="abs job-detail">Sed ut perspiciatis unde omnis iste natus error sit voluptatem accusantium doloremque laudantium, totam rem aperiam, sdjk eaque ipsa quae ab illo inventore</p>
      <svg class="abs job-pin" width="18" height="24" viewBox="0 0 18 24"><path d="M9 1C4.6 1 1.5 4.3 1.5 8.5 1.5 14 9 23 9 23s7.5-9 7.5-14.5C16.5 4.3 13.4 1 9 1z" fill="#555"/><circle cx="9" cy="8.5" r="3" fill="#fff"/></svg>
      <div class="abs job-place">Vestby</div>
    </article>

    <article class="abs job" style="top:843px">
      <div class="abs job-role">SENIOR CONSULTANT</div><div class="abs job-date">Mar 2018 - Present</div>
      <div class="abs job-dot"></div>
      <div class="abs job-company">Nordvik Systems</div>
      <div class="abs job-summary">Daudantium totam rem aperiam sdjk eaque ipsa quae</div>
      <p class="abs job-detail">Sed ut perspiciatis unde omnis iste natus error sit voluptatem accusantium doloremque laudantium, totam rem aperiam, sdjk eaque ipsa quae ab illo inventore</p>
      <svg class="abs job-pin" width="18" height="24" viewBox="0 0 18 24"><path d="M9 1C4.6 1 1.5 4.3 1.5 8.5 1.5 14 9 23 9 23s7.5-9 7.5-14.5C16.5 4.3 13.4 1 9 1z" fill="#555"/><circle cx="9" cy="8.5" r="3" fill="#fff"/></svg>
      <div class="abs job-place">Vestby</div>
    </article>

    <article class="abs job" style="top:1073px">
      <div class="abs job-role">SENIOR CONSULTANT</div><div class="abs job-date">Mar 2018 - Present</div>
      <div class="abs job-dot"></div>
      <div class="abs job-company">Nordvik Systems</div>
      <div class="abs job-summary">Daudantium totam rem aperiam sdjk eaque ipsa quae</div>
      <p class="abs job-detail">Sed ut perspiciatis unde omnis iste natus error sit voluptatem accusantium doloremque laudantium, totam rem aperiam, sdjk eaque ipsa quae ab illo inventore</p>
      <svg class="abs job-pin" width="18" height="24" viewBox="0 0 18 24"><path d="M9 1C4.6 1 1.5 4.3 1.5 8.5 1.5 14 9 23 9 23s7.5-9 7.5-14.5C16.5 4.3 13.4 1 9 1z" fill="#555"/><circle cx="9" cy="8.5" r="3" fill="#fff"/></svg>
      <div class="abs job-place">Vestby</div>
    </article>

    <article class="abs job" style="top:1303px">
      <div class="abs job-role">SENIOR CONSULTANT</div><div class="abs job-date">Mar 2018 - Present</div>
      <div class="abs job-dot"></div>
      <div class="abs job-company">Nordvik Systems</div>
      <div class="abs job-summary">Daudantium totam rem aperiam sdjk eaque ipsa quae</div>
      <p class="abs job-detail">Sed ut perspiciatis unde omnis iste natus error sit voluptatem accusantium doloremque laudantium, totam rem aperiam, sdjk eaque ipsa quae ab illo inventore</p>
      <svg class="abs job-pin" width="18" height="24" viewBox="0 0 18 24"><path d="M9 1C4.6 1 1.5 4.3 1.5 8.5 1.5 14 9 23 9 23s7.5-9 7.5-14.5C16.5 4.3 13.4 1 9 1z" fill="#555"/><circle cx="9" cy="8.5" r="3" fill="#fff"/></svg>
      <div class="abs job-place">Vestby</div>
    </article>
  </div>
</main>

<section class="skills">
  <h2 class="abs section-head" style="left:111px;top:106px">EDUCATION</h2>
  <div class="abs degree" style="top:174px">MS IN SOFTWARE ENGINEERING</div>
  <div class="abs school" style="top:204px">Sdoseisk University</div>
  <div class="abs period" style="top:234px">Mar 2004 - Apr 2006</div>
  <div class="abs degree" style="top:296px">BS IN COMPUTER SCIENCE</div>
  <div class="abs school" style="top:326px">Sdoseisk University</div>
  <div class="abs rule" style="left:111px;top:410px;width:438px"></div>

  <h2 class="abs section-head" style="left:111px;top:442px">OTHER SKILLS</h2>
  <div class="abs btn pill" style="left:113px;top:494px;width:106px">HTML5</div>
  <div class="abs btn pill" style="left:228px;top:494px;width:106px">JAVA</div>
  <div class="abs btn pill" style="left:345px;top:494px;width:106px">CSS3</div>
  <div class="abs btn pill" style="left:459px;top:494px;width:106px">SASS</div>
  <div class="abs btn pill" style="left:113px;top:566px;width:106px">GIT</div>
  <div class="abs btn pill" style="left:228px;top:566px;width:106px">CLOUD</div>
  <div class="abs btn pill" style="left:345px;top:566px;width:106px">SQL</div>
  <div class="abs btn pill" style="left:459px;top:566px;width:106px">.NET</div>
  <div class="abs btn pill" style="left:113px;top:638px;width:135px">BOOTSTRAP</div>
  <div class="abs btn pill" style="left:259px;top:638px;width:157px">MATERIAL DESIGN</div>

  <div class="abs vrule"></div>

  <h2 class="abs section-head" style="left:605px;top:106px">PROFESSIONAL SKILLS</h2>
  <div class="abs" style="left:609px;top:143px;font-size:13px;font-family:'Archivo',Arial,sans-serif">Top Skills</div>

  <div class="abs skill-name" style="top:174px">JAVASCRIPT</div>
  <div class="abs skill-level" style="top:208px">Expert</div>
  <p class="abs skill-desc" style="top:230px">Sed ut perspiciatis unde omnis iste natus error sit voluptatem accusantium doloremque laudantium.</p>
  <div class="abs bar" style="top:286px"><div class="abs bar-fill" style="width:455px"></div></div>

  <div class="abs skill-name" style="top:338px">ANGULAR</div>
  <div class="abs skill-level" style="top:372px">Advance</div>
  <p class="abs skill-desc" style="top:394px">Sed ut perspiciatis unde omnis iste natus error sit voluptatem accusantium doloremque laudantium.</p>
  <div class="abs bar" style="top:452px"><div class="abs bar-fill" style="width:408px"></div></div>

  <div class="abs skill-name" style="top:502px">TYPESCRIPT</div>
  <div class="abs skill-level" style="top:536px">Advance</div>
  <p class="abs skill-desc" style="top:558px">Sed ut perspiciatis unde omnis iste natus error sit voluptatem accusantium doloremque laudantium.</p>
  <div class="abs bar" style="top:618px"><div class="abs bar-fill" style="width:325px"></div></div>
</section>

<section class="portfolio">
  <h2 class="abs portfolio-title">PORTFOLIO</h2>
  <div class="abs shot" style="left:111px;top:168px;width:334px;height:186px;background:linear-gradient(135deg,#eef2fb,#c9d6f5 60%,#8aa3ea)" role="img" aria-label="Portfolio project: web design landing page for agencies"></div>
  <div class="abs shot" style="left:490px;top:168px;width:281px;height:186px;background:linear-gradient(135deg,#dfe9f5,#b7cbe6 55%,#5b6f9a)" role="img" aria-label="Portfolio project: innovative websites landing page"></div>
  <div class="abs shot" style="left:815px;top:168px;width:272px;height:186px;background:linear-gradient(135deg,#f3f5fc,#dbe3f7 60%,#b8c6ef)" role="img" aria-label="Portfolio project: website analytics landing page"></div>
  <div class="abs shot" style="left:115px;top:395px;width:315px;height:203px;background:linear-gradient(135deg,#c7c7c7,#2f4f5e 50%,#c9c9c9)" role="img" aria-label="Portfolio project: dark teal multi-page web design"></div>
  <div class="abs shot" style="left:492px;top:395px;width:219px;height:203px;background:linear-gradient(135deg,#f0f0f0,#e9c33a 45%,#c7302a 70%,#f2f2f2)" role="img" aria-label="Portfolio project: yellow and red web design pages"></div>
  <div class="abs shot" style="left:775px;top:395px;width:313px;height:203px;background:linear-gradient(135deg,#c9c9c9,#8e5bb8 40%,#e59a3c 70%,#d0d0d0)" role="img" aria-label="Portfolio project: purple and orange web design pages"></div>
  <a class="abs btn view-more">VIEW MORE</a>
</section>

<footer class="site-footer">Copyrights © 2020 All Rights Reserved</footer>

</body>
</html>
```